Popup Nightclub Grand Opening Flyer

We need to design a flyer for the grand opening of an upscale, exclusive nightclub called "Lantern". The design needs to be chic and exclusive. The background should be black and the text should primarily be white. We like minimalist designs.

Here is the text for the flyer
-
Velvetroll Atlanta Presents

Lantern (LOGO)

A Popup Nightclub Experience
For one night Only

Friday, October 18, 2013
Party begins at 9PM

INVITE ONLY

See invitation for location details
(Velvetroll Atlanta logo)

-
Examples we like

http://cdn4-x.pressfolio-example.com/sites/default/files/styles/image_content_width/hash/3b/fd/2468013579_4421_flyer.jpg?itok=K9rtQw2z

http://files.hubspace-example.net/files/8Hqq-Tr72WWE3kaRbTmcxP5QZK2F396J8nbRw4CKMHfdX2Y7qSEF-MqjxDoNrLY3QCyQJD7npjGaRq3k-Mhx6hqf3MDSWf8r3/2zenSaturdays.jpg

http://morvex-example.com/wp-content/uploads/siteskin/widgetkit/gallery/2zen/2zen-gen_qstay4-01.jpg

Hi All, one thing that we are seeing that we don't like is on over emphasis on the phrase "a popup nightclub experience" please don't make this the largest thing on the flyer

Target Market(s)

Target market is 25-35 year olds who are affluent (rich) and like luxury brands

Requirements
Must have
• Dark Background
Nice to have
• Velvetroll Logo on the bottom
Modern text that isn't curvy
Should not have
• Curved text

```html
<!DOCTYPE html>
<html lang="en">
<head>
<meta charset="utf-8">
<title>Lantern Nightclub – Popup Flyer</title>
<link href="https://fonts.googleapis.com/css2?family=Montserrat:wght@500;600;700&family=Questrial&display=swap" rel="stylesheet">
<style>
  :root {
    --night: #000000;
    --damask-olive: #3b3a14;
    --damask-deep: #16150a;
    --white: #ffffff;
    --silver: #c9c9c9;
    --steel: #9b9b9b;
    --slate: #8a8a8a;
    --gold: #c4c01f;
    --gold-glow: rgba(220, 214, 40, 0.55);
    --rule: #d8d8d8;
  }
  * { margin: 0; padding: 0; box-sizing: border-box; }
  html, body {
    width: 787px; height: 1200px; overflow: hidden; background: var(--night);
  }
  .flyer {
    position: relative; width: 787px; height: 1200px; overflow: hidden;
    background: var(--night); color: var(--white);
    font-family: "Questrial", "Century Gothic", sans-serif;
    text-align: center;
  }
  .damask-backdrop {
    position: absolute; left: 0; top: 0; width: 787px; height: 900px;
    background:
      radial-gradient(ellipse 70% 55% at 50% 38%, var(--damask-olive) 0%, var(--damask-deep) 60%, rgba(0,0,0,0) 100%),
      linear-gradient(to bottom, var(--damask-deep) 0%, var(--damask-deep) 55%, var(--night) 100%);
  }
  .line { position: absolute; left: 0; width: 100%; }
  .presenter {
    top: 26px; font-family: "Montserrat", sans-serif; font-weight: 600;
    font-size: 20px; letter-spacing: 0.5px;
  }
  .club-mark {
    position: absolute; left: 228px; top: 250px; width: 330px; height: 330px;
    border-radius: 50%;
    background: linear-gradient(135deg, #f2f2f2 0%, #9a9a9a 50%, #4a4a4a 100%);
  }
  .club-name {
    top: 655px; font-size: 54px; letter-spacing: 9px; color: var(--silver);
    line-height: 1;
  }
  .club-type {
    top: 716px; font-size: 24px; letter-spacing: 4px; color: var(--silver);
  }
  .tagline {
    top: 772px; font-family: "Montserrat", sans-serif; font-weight: 600;
    font-size: 31px; letter-spacing: 0.3px;
  }
  .tagline-rule {
    position: absolute; left: 106px; top: 822px; width: 588px; height: 2px;
    background: var(--rule);
  }
  .headline {
    top: 838px; font-family: "Montserrat", sans-serif; font-weight: 600;
    font-size: 44px; color: var(--gold); letter-spacing: 0.5px;
    text-shadow: 0 0 14px var(--gold-glow);
  }
  .event-date {
    top: 904px; font-family: "Montserrat", sans-serif; font-weight: 600;
    font-size: 26px; letter-spacing: 1.5px; color: var(--slate);
  }
  .access {
    top: 1006px; font-family: "Montserrat", sans-serif; font-weight: 600;
    font-size: 26px;
  }
  .access-note {
    top: 1051px; font-family: "Montserrat", sans-serif; font-weight: 500;
    font-size: 12px;
  }
  .host-mark {
    position: absolute; left: 0; top: 1098px; width: 100%;
    display: flex; justify-content: center; align-items: center; gap: 16px;
  }
  .host-dot {
    width: 30px; height: 30px; border-radius: 50%; background: var(--silver);
  }
  .host-name {
    font-size: 26px; letter-spacing: 2px; color: var(--white);
  }
</style>
</head>
<body>
  <main class="flyer">
    <div class="damask-backdrop" role="img" aria-label="Dark olive damask scroll pattern fading into black"></div>

    <p class="line presenter">VELVETROLL ATLANTA PRESENTS</p>

    <div class="club-mark" aria-hidden="true"></div>
    <h1 class="line club-name">LANTERN</h1>
    <p class="line club-type">NIGHTCLUB</p>

    <p class="line tagline">A POPUP NIGHTCLUB EXPERIENCE</p>
    <div class="tagline-rule"></div>
    <p class="line headline">FOR ONE NIGHT ONLY</p>
    <p class="line event-date">FRIDAY OCTOBER 18 2013 @ 9:00PM</p>

    <p class="line access">INVITE ONLY</p>
    <p class="line access-note">SEE INVITATION FOR LOCATION DETAILS</p>

    <div class="host-mark">
      <span class="host-dot" aria-hidden="true"></span>
      <span class="host-name">VELVETROLL ATLANTA</span>
    </div>
  </main>
</body>
</html>
```